Home Remodeling company needs a business card design

we need a business card design for home remodeling company in hamilton county, indiana USA. we offers a wide range of construction services including whole house renovations, Design and Build Basements and Kitchen and Bathroom Remodeling . we would like to see designs for both site of business card that use the same color of the company logo and also including all information below :
1- Karim Feltous CEO / General Contractor
2- all company contacts Telephone numbers ( 1-888-DULOM-47 ) ( 317-555-0193) email address ( info@dulomhome.com) website ( www.dulomhome.com ) and social media logos (Facebook- twitter- google plus )
3- company logo
4- licensed . insured . bonded

```html
<!DOCTYPE html>
<html lang="en">
<head>
<meta charset="utf-8">
<title>Dulom — Business Card</title>
<link rel="stylesheet" href="https://fonts.googleapis.com/css2?family=Arimo:wght@400;700&family=Bodoni+Moda:wght@500&display=swap">
<style>
  :root {
    --red: #c9303a;
    --ink: #3a3a3c;
    --gray: #6b6b6d;
    --black: #000000;
    --white: #ffffff;
    --backdrop: #dcdcdc;
  }
  * { margin: 0; padding: 0; box-sizing: border-box; }
  html, body {
    width: 1189px; height: 1200px; overflow: hidden;
    background: var(--backdrop);
    font-family: "Arimo", Arial, sans-serif;
  }
  .card {
    position: absolute; left: 140px;
    width: 918px; height: 524px;
    background: var(--white);
    overflow: hidden;
  }
  .card--front { top: 45px; }
  .card--back { top: 623px; }

  .company-name {
    position: absolute; left: 0; width: 100%;
    text-align: center;
    font-family: "Arimo", Arial, sans-serif; font-weight: 700;
    color: var(--ink); line-height: 1;
  }
  .card--front .company-name { top: 62px; font-size: 84px; }
  .card--back .company-name { top: 205px; font-size: 110px; }

  .tagline {
    position: absolute; left: 0; width: 100%; top: 177px;
    text-align: center; font-size: 27px; color: #111; letter-spacing: 0.2px;
  }
  .wave { position: absolute; left: 0; top: 0; width: 918px; height: 524px; }

  .person { position: absolute; left: 33px; top: 318px; }
  .person__name {
    font-family: "Bodoni Moda", "Didot", serif; font-weight: 500;
    font-size: 50px; line-height: 1.05; color: var(--red);
  }
  .person__role { margin-top: 10px; font-size: 25px; color: var(--white); }

  .social { position: absolute; left: 38px; top: 440px; display: flex; gap: 18px; }
  .social__item { width: 58px; height: 55px; border-radius: 6px; }
  .social__item--a { background: var(--red); }
  .social__item--b { background: var(--gray); }
  .social__item--c { background: var(--ink); }

  .contacts { position: absolute; right: 34px; top: 362px; list-style: none; }
  .contacts__item {
    display: flex; align-items: center; justify-content: flex-end;
    height: 35.5px; font-size: 26px; color: var(--white);
  }
  .contacts__icon { width: 21px; height: 21px; margin-left: 17px; flex: none; }
</style>
</head>
<body>

<section class="card card--front" aria-label="Business card front">
  <svg class="wave" viewBox="0 0 918 524" aria-hidden="true">
    <path fill="var(--red)" d="M0,237 C200,290 460,288 700,223 L700,524 L0,524 Z"/>
    <path fill="var(--black)" d="M0,290 C120,318 330,320 520,268 C600,240 650,224 700,223 C790,222 860,250 918,282 L918,524 L0,524 Z"/>
  </svg>

  <p class="company-name">DULOM</p>
  <p class="tagline">licensed .insured . bonded</p>

  <div class="person">
    <h1 class="person__name">Karim Feltous</h1>
    <p class="person__role">CEO / General Contractor</p>
  </div>

  <div class="social" aria-label="Social media">
    <span class="social__item social__item--a"></span>
    <span class="social__item social__item--b"></span>
    <span class="social__item social__item--c"></span>
  </div>

  <ul class="contacts">
    <li class="contacts__item">317-555-0193
      <svg class="contacts__icon" viewBox="0 0 21 21" aria-hidden="true"><rect width="21" height="21" fill="var(--red)"/><path d="M7 4 L9 7 L8 9 Q9 12 12 13 L14 12 L17 14 L15 17 Q9 17 5 11 Q4 6 7 4 Z" fill="var(--white)"/></svg></li>
    <li class="contacts__item">1-888-DULOM-47
      <svg class="contacts__icon" viewBox="0 0 21 21" aria-hidden="true"><rect width="21" height="21" fill="var(--red)"/><path d="M7 4 L9 7 L8 9 Q9 12 12 13 L14 12 L17 14 L15 17 Q9 17 5 11 Q4 6 7 4 Z" fill="var(--white)"/></svg></li>
    <li class="contacts__item">www.dulomhome.com
      <svg class="contacts__icon" viewBox="0 0 21 21" aria-hidden="true"><rect width="21" height="21" fill="var(--red)"/><circle cx="10.5" cy="10.5" r="7" fill="none" stroke="var(--white)" stroke-width="1.6"/><path d="M3.5 10.5 H17.5 M10.5 3.5 Q6 10.5 10.5 17.5 M10.5 3.5 Q15 10.5 10.5 17.5" fill="none" stroke="var(--white)" stroke-width="1.3"/></svg></li>
    <li class="contacts__item">info@dulomhome.com
      <svg class="contacts__icon" viewBox="0 0 21 21" aria-hidden="true"><rect width="21" height="21" fill="var(--red)"/><rect x="4" y="6" width="13" height="9" fill="none" stroke="var(--white)" stroke-width="1.5"/><path d="M4 6 L10.5 11 L17 6" fill="none" stroke="var(--white)" stroke-width="1.5"/></svg></li>
  </ul>
</section>

<section class="card card--back" aria-label="Business card back">
  <p class="company-name">DULOM</p>
</section>

</body>
</html>
```